New web page, 2 companies on the one page

A new web page for an engineering consultancy and maintenance management company

Corlett & Associates is the parent company covering the design and consultancy
Valtrix Engineering is the Maintenance and Reliability company

Target Market(s)

Food & Beverage, ingredients Manufacturing
engineering managers

Coding

Coded - Design and coding required

Number of Pages Required

1 page

Font styles to use
Other font styles liked:
• Roboto

Colors
1861ab
85acd3
d0dfed
cee9f5

```html
<!DOCTYPE html>
<html lang="en">
<head>
<meta charset="utf-8">
<title>Corlett &amp; Associates</title>
<link href="https://fonts.googleapis.com/css2?family=Michroma&family=Roboto:wght@300;400;500;700&display=swap" rel="stylesheet">
<style>
:root{
  --brand-blue:#1c8fd6;
  --deep-blue:#1861ab;
  --soft-blue:#85acd3;
  --pale-blue:#d0dfed;
  --sky-blue:#c6e4f3;
  --ink:#141414;
  --stripe-grey:#5f5f61;
  --footer-dark:#1b1819;
  --muted:#9a9a9a;
  --icon:#4f6f96;
}
*{box-sizing:border-box;margin:0;padding:0}
html,body{width:1200px;height:3750px;overflow:hidden}
body{position:relative;background:#fff;font-family:"Roboto",Arial,sans-serif;color:var(--ink)}
.backdrop{position:absolute;left:0;top:0;width:1200px;height:3750px;z-index:0}
.layer{position:absolute;z-index:1}

/* header */
.top-rule{left:0;top:0;width:1200px;height:3px;background:var(--soft-blue)}
.brand{left:144px;top:20px;display:flex;align-items:center;gap:10px}
.brand-mark{width:30px;height:30px;background:var(--deep-blue)}
.brand-name{font-weight:700;font-size:20px;color:#2b2b2b;letter-spacing:.5px}
.main-nav{left:530px;top:29px;display:flex;gap:0;font-size:14px;font-weight:500}
.main-nav a{text-decoration:none;color:#222;margin-right:32px}
.main-nav a.active{color:var(--brand-blue)}
.main-nav .home-dot{display:inline-block;width:12px;height:12px;border-radius:50%;border:2px solid var(--deep-blue);margin-right:6px;vertical-align:-1px}
.search-btn{left:1019px;top:21px;width:36px;height:36px;border-radius:50%;background:var(--soft-blue)}

/* hero */
.hero-title{left:0;top:205px;width:1200px;text-align:center;font-family:"Michroma",sans-serif;font-size:64px;line-height:95px;color:#fff;letter-spacing:3px;text-shadow:0 2px 6px rgba(0,0,0,.35)}
.hero-sub{left:0;top:408px;width:1200px;text-align:center;font-size:27px;font-weight:500;color:#fff;letter-spacing:-.4px;text-shadow:0 2px 4px rgba(0,0,0,.6)}
.btn{display:flex;align-items:center;justify-content:center;border-radius:30px;color:#fff;font-size:16px;font-weight:500;text-transform:uppercase}
.btn-fill{background:var(--soft-blue)}
.btn-line{border:2px solid #fff}
.get-started{left:405px;top:498px;width:189px;height:58px}
.learn-more{left:604px;top:498px;width:192px;height:58px}
.slide-dots{left:566px;top:654px;display:flex;gap:10px}
.slide-dots span{width:6px;height:6px;border-radius:50%;background:#fff}
.slide-dots span.on{background:var(--brand-blue)}

/* headings */
.section-title{font-family:"Michroma",sans-serif;font-size:38px;letter-spacing:3px;color:var(--ink);white-space:nowrap}
.section-title em{font-style:normal;color:var(--brand-blue)}

/* about */
.about-emblem{left:144px;top:856px;width:390px;height:408px;background:linear-gradient(135deg,#1d1d1f 0%,#3a3f46 45%,#1d3c5a 75%,#0f2233 100%);border-radius:6px}
.about-title{left:619px;top:893px}
.about-copy{left:619px;top:968px;width:440px;font-size:13px;line-height:24px;color:var(--muted);font-weight:300}
.read-more{left:619px;top:1160px;width:161px;height:59px}

/* services */
.services-title{left:0;top:1528px;width:1200px;text-align:center}
.service-grid{left:144px;top:1637px;width:911px;display:grid;grid-template-columns:repeat(4,214px);column-gap:18px;row-gap:18px}
.service-card{height:198px;background:#fff;border-radius:6px;box-shadow:0 3px 6px rgba(40,70,100,.18);display:flex;flex-direction:column;align-items:center;padding-top:18px;text-align:center}
.service-card svg{width:74px;height:74px}
.service-card h3{margin-top:14px;font-size:16px;font-weight:500;line-height:22px;color:#1e1e1e;padding:0 18px}
.services-more{left:520px;top:2105px;width:161px;height:59px}

/* gallery */
.gallery-title{left:0;top:2431px;width:1200px;text-align:center}
.gallery-grid{left:144px;top:2531px;display:grid;grid-template-columns:296px 296px 296px;column-gap:12px;row-gap:13px}
.gallery-item{height:200px}
.g1{background:linear-gradient(135deg,#1c2f4c,#3a5f86 50%,#0e1a2b)}
.g2{background:linear-gradient(135deg,#6b5a45,#a8906d 50%,#3c3128)}
.g3{background:linear-gradient(135deg,#c9cdd2,#8a8d91 50%,#3f4a59)}
.g4{background:linear-gradient(135deg,#6d5c4b,#b9ac9a 55%,#4d4036)}
.g5{background:linear-gradient(135deg,#0d2140,#2d5d96 50%,#0a1a33)}
.g6{background:linear-gradient(180deg,#1a4f88,#3b7fc0 50%,#0d2f5e)}
.gallery-more{left:520px;top:2986px;width:161px;height:59px}

/* footer */
.footer-brand{left:0;top:3272px;width:1200px;display:flex;justify-content:center;align-items:center;gap:14px}
.footer-brand-mark{width:40px;height:40px;border-radius:50%;background:var(--brand-blue)}
.footer-brand-name{font-family:"Michroma",sans-serif;font-size:24px;color:#fff;letter-spacing:1px}
.footer-head{font-size:14px;font-weight:500;color:#fff;text-transform:uppercase}
.touch-head{left:153px;top:3403px}
.contact-head{left:783px;top:3403px}
.field{position:absolute;background:#fff;border:none;font-family:"Roboto",sans-serif;font-size:10px;color:#777;padding:0 13px;resize:none}
.field::placeholder{color:#777}
.f-name{left:154px;top:3443px;width:277px;height:28px}
.f-phone{left:441px;top:3443px;width:277px;height:28px}
.f-email{left:154px;top:3484px;width:564px;height:28px}
.f-message{left:154px;top:3525px;width:564px;height:66px;padding-top:8px}
.submit{left:638px;top:3604px;width:80px;height:28px;font-size:12px;border-radius:14px}
.contact-row{position:absolute;left:783px;display:flex;align-items:center;gap:19px;font-size:12px;line-height:18px;color:#fff}
.contact-row svg{width:34px;height:34px;flex:none}
.row-address{top:3445px}
.row-phone{top:3492px}
.row-email{top:3540px}
.social{left:787px;top:3594px;display:flex;gap:4px}
.social span{width:28px;height:28px;border-radius:50%}
.social .s1{background:var(--deep-blue)}
.social .s2{background:var(--brand-blue)}
.social .s3{background:var(--soft-blue)}
.social .s4{background:var(--pale-blue)}
.footer-rule{left:131px;top:3679px;width:936px;height:1px;background:#3a3738}
.copyright{left:0;top:3707px;width:1200px;text-align:center;font-size:12px;color:#fff}
</style>
</head>
<body>

<svg class="backdrop" viewBox="0 0 1200 3750" aria-hidden="false">
  <defs>
    <linearGradient id="heroSky" x1="0" y1="0" x2="0" y2="1">
      <stop offset="0" stop-color="#3a3c78"/>
      <stop offset=".35" stop-color="#6a5a8c"/>
      <stop offset=".55" stop-color="#4a4a6a"/>
      <stop offset=".75" stop-color="#263a5c"/>
      <stop offset="1" stop-color="#16284a"/>
    </linearGradient>
    <linearGradient id="skyline" x1="0" y1="0" x2="0" y2="1">
      <stop offset="0" stop-color="#ffffff"/>
      <stop offset="1" stop-color="#d6e7f5"/>
    </linearGradient>
  </defs>
  <rect role="img" aria-label="Harbour bridge and opera house at dusk with city lights" x="0" y="77" width="1200" height="725" fill="url(#heroSky)"/>
  <polygon points="0,606 597,784 597,797 0,619" fill="var(--stripe-grey)"/>
  <polygon points="603,784 1200,606 1200,619 603,797" fill="var(--brand-blue)"/>
  <polygon points="0,619 597,797 603,797 1200,619 1200,900 0,900" fill="#fff"/>

  <polygon points="0,1208 600,1420 1200,1208 1200,2150 603,2328 597,2328 0,2150" fill="var(--sky-blue)"/>
  <polygon points="0,2150 597,2328 597,2341 0,2163" fill="var(--stripe-grey)"/>
  <polygon points="603,2328 1200,2150 1200,2163 603,2341" fill="var(--brand-blue)"/>

  <rect role="img" aria-label="Faint line drawing of a city skyline with a ferris wheel" x="0" y="2960" width="1200" height="340" fill="url(#skyline)"/>
  <polygon points="0,3286 597,3126 597,3139 0,3299" fill="var(--brand-blue)"/>
  <polygon points="603,3126 1200,3286 1200,3299 603,3139" fill="var(--stripe-grey)"/>
  <polygon points="0,3299 597,3139 603,3139 1200,3299 1200,3750 0,3750" fill="var(--footer-dark)"/>
</svg>

<header>
  <div class="layer top-rule"></div>
  <div class="layer brand"><span class="brand-mark"></span><span class="brand-name">CORLETT &amp; ASSOCIATES</span></div>
  <nav class="layer main-nav">
    <a class="active" href="#"><span class="home-dot"></span>HOME</a>
    <a href="#">ABOUT US</a>
    <a href="#">SERVICES</a>
    <a href="#">NEWS</a>
    <a href="#">CONTACT US</a>
  </nav>
  <div class="layer search-btn">
    <svg viewBox="0 0 36 36" width="36" height="36"><circle cx="17" cy="17" r="5" fill="none" stroke="#fff" stroke-width="2"/><line x1="20.5" y1="20.5" x2="24" y2="24" stroke="#fff" stroke-width="2.4" stroke-linecap="round"/></svg>
  </div>
</header>

<section class="hero">
  <h1 class="layer hero-title">CORLETT<br>ASSOCIATES</h1>
  <p class="layer hero-sub">Lorem ipsum dolor sit ametconsectetur adipiscing elit</p>
  <a class="layer btn btn-fill get-started">Get Started</a>
  <a class="layer btn btn-line learn-more">Learn More</a>
  <div class="layer slide-dots"><span></span><span></span><span class="on"></span><span></span><span></span></div>
</section>

<section class="about">
  <div class="layer about-emblem" role="img" aria-label="Company emblem filled with dark abstract light-trail imagery"></div>
  <h2 class="layer section-title about-title">ABOUT <em>US</em></h2>
  <p class="layer about-copy">Corlett &amp; Associates is specialised manufacturing engineering support organisation that can provide fast, nimble, and flexible services. We have a proven track record in delivering tangible outcomes in process design and fit-out, project management, manufacturing process and maintenance design and execution.Our specialist focus in food manufacturing across a range of sectors allows our team to deliver real benefits to performance and recognition of the clients investment.</p>
  <a class="layer btn btn-fill read-more">Read More</a>
</section>

<section class="services">
  <h2 class="layer section-title services-title">OUR <em>SERVICES</em></h2>
  <div class="layer service-grid">
    <article class="service-card">
      <svg viewBox="0 0 64 64" fill="none" stroke="var(--icon)" stroke-width="1.8"><path d="M6 58V30l12 8v-8l12 8v-8l12 8V14h10v44z"/><line x1="4" y1="58" x2="60" y2="58"/><rect x="12" y="44" width="6" height="6"/><rect x="26" y="44" width="6" height="6"/><rect x="40" y="44" width="6" height="6"/><circle cx="47" cy="8" r="4" stroke="var(--brand-blue)"/></svg>
      <h3>Process &amp; Facilities Design</h3>
    </article>
    <article class="service-card">
      <svg viewBox="0 0 64 64" fill="none" stroke="var(--icon)" stroke-width="1.8"><path d="M14 6h26l10 10v42H14z"/><path d="M40 6v10h10"/><circle cx="32" cy="36" r="9"/><circle cx="32" cy="36" r="3.5" stroke="var(--brand-blue)"/><path d="M32 24v3M32 45v3M20 36h3M41 36h3"/></svg>
      <h3>Project Management</h3>
    </article>
    <article class="service-card">
      <svg viewBox="0 0 64 64" fill="none" stroke="var(--icon)" stroke-width="1.8"><rect x="8" y="6" width="28" height="50"/><path d="M8 16h28M8 26h28M14 46v6M19 42v10M24 46v6"/><circle cx="46" cy="42" r="8" stroke="var(--brand-blue)"/><circle cx="46" cy="42" r="3"/><path d="M46 30v4M46 50v4M34 42h4M54 42h4"/></svg>
      <h3>Major Equipment and Services Installation &amp; Commissioning</h3>
    </article>
    <article class="service-card">
      <svg viewBox="0 0 64 64" fill="none" stroke="var(--icon)" stroke-width="1.8"><path d="M18 26a14 14 0 0 1 28 0"/><path d="M14 26h36"/><path d="M32 12v8" stroke="var(--brand-blue)"/><rect x="22" y="30" width="20" height="10" rx="3"/><path d="M12 58v-8a8 8 0 0 1 8-8h24a8 8 0 0 1 8 8v8z"/></svg>
      <h3>Engineering &amp; Maintenance Management</h3>
    </article>
    <article class="service-card">
      <svg viewBox="0 0 64 64" fill="none" stroke="var(--icon)" stroke-width="1.8"><circle cx="32" cy="28" r="16"/><circle cx="32" cy="28" r="6" stroke="var(--brand-blue)"/><path d="M32 8v4M32 44v4M12 28h4M48 28h4"/><path d="M27 44v14h10V44"/></svg>
      <h3>Maintenance Execution</h3>
    </article>
    <article class="service-card">
      <svg viewBox="0 0 64 64" fill="none" stroke="var(--icon)" stroke-width="1.8"><circle cx="32" cy="32" r="25"/><circle cx="32" cy="32" r="18"/><path d="M32 32l9-9" stroke="var(--brand-blue)" stroke-width="2.4"/><circle cx="32" cy="32" r="2.5"/><path d="M20 44h24"/></svg>
      <h3>Manufacturing Performance Measurement</h3>
    </article>
    <article class="service-card">
      <svg viewBox="0 0 64 64" fill="none" stroke="var(--icon)" stroke-width="1.8"><circle cx="36" cy="26" r="16"/><path d="M26 28l6-6 5 5 8-8" stroke="var(--brand-blue)"/><path d="M24 38L8 54l4 4 16-16"/></svg>
      <h3>Vision Inspection Systems</h3>
    </article>
    <article class="service-card">
      <svg viewBox="0 0 64 64" fill="none" stroke="var(--icon)" stroke-width="1.8"><rect x="6" y="20" width="38" height="38"/><path d="M6 34h16v14h22M22 20v8"/><circle cx="47" cy="17" r="8" stroke="var(--brand-blue)"/><circle cx="47" cy="17" r="3"/><path d="M47 5v4M47 25v4M35 17h4M55 17h4"/></svg>
      <h3>Acquisition Due Diligence</h3>
    </article>
  </div>
  <a class="layer btn btn-fill services-more">View More</a>
</section>

<section class="gallery">
  <h2 class="layer section-title gallery-title">PROJECT <em>GALLERY</em></h2>
  <div class="layer gallery-grid">
    <div class="gallery-item g1" role="img" aria-label="Hand holding a tablet with glowing data in a factory"></div>
    <div class="gallery-item g2" role="img" aria-label="Laptop on a wooden desk with maintenance planning notes and coffee"></div>
    <div class="gallery-item g3" role="img" aria-label="Engineering team in hard hats meeting around a table"></div>
    <div class="gallery-item g4" role="img" aria-label="Two engineers reviewing drawings on a site table"></div>
    <div class="gallery-item g5" role="img" aria-label="Figure facing large digital dashboard screens"></div>
    <div class="gallery-item g6" role="img" aria-label="Abstract blue data streams between server towers"></div>
  </div>
  <a class="layer btn btn-fill gallery-more">View More</a>
</section>

<footer>
  <div class="layer footer-brand"><span class="footer-brand-mark"></span><span class="footer-brand-name">VALTRIX ENGINEERING</span></div>

  <h4 class="layer footer-head touch-head">Get in touch</h4>
  <input class="field f-name" type="text" placeholder="Name :">
  <input class="field f-phone" type="text" placeholder="Phone :">
  <input class="field f-email" type="text" placeholder="Email :">
  <textarea class="field f-message" placeholder="Message :"></textarea>
  <a class="layer btn btn-fill submit">Submit</a>

  <h4 class="layer footer-head contact-head">Contact information</h4>
  <div class="contact-row row-address">
    <svg viewBox="0 0 34 34" fill="none" stroke="#fff" stroke-width="1.4"><circle cx="17" cy="17" r="15.5"/><path d="M17 25s-5-5.5-5-9a5 5 0 0 1 10 0c0 3.5-5 9-5 9z" fill="#fff" stroke="none"/><circle cx="17" cy="16" r="1.8" fill="var(--footer-dark)" stroke="none"/></svg>
    <span>122,Lorem ipsum dolor sit amet<br>consectetur adipiscing elit</span>
  </div>
  <div class="contact-row row-phone">
    <svg viewBox="0 0 34 34" fill="none" stroke="#fff" stroke-width="1.4"><circle cx="17" cy="17" r="15.5"/><path d="M12 11l3 0 1.5 4-2 1.5a9 9 0 0 0 4 4l1.5-2 4 1.5v3c-7 1-13-5-12-12z" fill="#fff" stroke="none"/></svg>
    <span>Telephone: 1 888 888 8888</span>
  </div>
  <div class="contact-row row-email">
    <svg viewBox="0 0 34 34" fill="none" stroke="#fff" stroke-width="1.4"><circle cx="17" cy="17" r="15.5"/><rect x="10" y="12" width="14" height="10" fill="#fff" stroke="none"/><path d="M10 12l7 6 7-6" stroke="var(--footer-dark)"/></svg>
    <span>Email : info@corlettassociates.com</span>
  </div>
  <div class="layer social" aria-label="Social links"><span class="s1"></span><span class="s2"></span><span class="s3"></span><span class="s4"></span></div>

  <div class="layer footer-rule"></div>
  <p class="layer copyright">Copyrights © 2021,Corlett Associates.All Rights Reserved. &nbsp;|&nbsp; Privacy policy &nbsp;|&nbsp; Terms and Conditions</p>
</footer>

</body>
</html>
```